Generate website for parcelnook.com

Please design a website for our business. It must be clean, streamlined and obvious.

Our business combines ecommerce, with social networking, and zorvi maps. The logo is a shopping bag (ecommerce) and honeycombs inside representing the various compartments of business that are offered throughout site.

Clients use our site to visit the interior of stores and restaurants through video streaming and can virtually "walk through" the store and purchase items with friends and loved ones through the web.

We want to incorporate this logo with the work that we are doing and play on this honeycomb theme.

Our business is "parcelnook.com" because we are all about "u"!

Please make homepage with about us tab, contact us form, mission tab, we also want a page with our research links included that bolster the case for our startup.

We will incorporate a small video on the front screen. A homepage like fildrawer.com only this time with our parcelnook!

Also include, COMING SOON, on the homepage please.
Updates

These are some good templates/example sites of clean and simple but effective: https://7elmrow.com/preview www.fildrawer.com

We are excited to see your submissions. Currently, a very good and only one designer has posted so far. Let us know!

Please include the TM (trademark) symbol after the logo, the name, and the slogan throughout the website. Thank you!

Put the TM after the LOGO and after the slogan "Placement ran Supreme" Lorcan

Target Market(s)

We will begin with female online shoppers.

Industry/Entity Type

Shopping

Font styles to use
Serif
Sans Serif

Colors
e567a6
fece3e
85cae6

Requirements
Must have
• Clean Look
Simple like Fildrawer with simple options "see film" or login/signup.

With browser tabs at the bottom much like fildrawer.

1. Shopper when opening Parcelnook.com website will see a simple webpage with a large Parcelnook logo in the center.

2. User will see log-in and password or create account in upper right hand corner of webpage. Mobile device website will be underneath logo.

3.We Prefer a background for webpages adding a softer experience on the the eyes of the user. A photo in the background to show shopretail experience.

4. Clicking on theParcelnook logo will inform users of details and instructions about platform. Example: About, contact, mission, Help etc. Logo will become somewhat like an interactive tool for help and guidance.

5. Parcelnook is currently scouting for it's founding venues. A founding venue will be the first venues to appear to the public on the Parcelnook platform. Founding venues (FV) will inherit a lifetime of the lowest possible rates of 2%* for the duration of it's business. All businesses wishing to participate in the founding venues offer please leave your email address and store name and a representative will get back with you.

*Venues will be subjected to credit card and CoinTrail rates in addition.

Nice to have
• http://www.zorvi.com/patents/US5193774

Must include the link above/visual of this page on the site as well.

```html
<!DOCTYPE html>
<html lang="en">
<head>
<meta charset="utf-8">
<title>Parcelnook.com — Coming Soon</title>
<link rel="stylesheet" href="https://fonts.googleapis.com/css2?family=Dancing+Script:wght@700&family=Nunito:wght@800&family=Tinos:ital@1&display=swap">
<style>
  :root {
    --night: #000000;
    --ink-white: #ffffff;
    --rule-grey: #9a9a9a;
    --band-grey: #777777;
    --panel-top: #6a9fb4;
    --panel-mid: #0b3a4d;
    --panel-low: #02020e;
    --button-green: #a9c97c;
    --button-edge: #c9a64a;
    --button-ring: #7fb2c8;
    --tab-pink: #e567a6;
    --tab-cream: #fde9bd;
    --script: "Dancing Script", cursive;
    --brand: "Nunito", sans-serif;
    --serif: "Tinos", serif;
  }
  * { box-sizing: border-box; margin: 0; padding: 0; }
  html, body { width: 1200px; height: 1091px; overflow: hidden; background: var(--ink-white); }
  .page { position: relative; width: 1200px; height: 1091px; }

  .stage { position: absolute; left: 0; top: 0; width: 1200px; height: 745px; background: var(--night); }
  .stage-band { position: absolute; left: 0; top: 745px; width: 1200px; height: 15px; background: var(--band-grey); }

  .coming-soon {
    position: absolute; left: 752px; top: 40px; width: 448px; height: 66px;
    border-bottom: 1px solid var(--rule-grey);
    font-family: var(--script); font-size: 48px; color: var(--ink-white);
    letter-spacing: 2px; text-align: right; padding-right: 44px; line-height: 64px;
  }

  .brand { position: absolute; left: 311px; top: 153px; display: flex; align-items: flex-end; gap: 30px; }
  .brand-mark { width: 117px; height: 207px; background: var(--ink-white); }
  .brand-name {
    font-family: var(--brand); font-weight: 800; font-size: 82px; line-height: 1;
    color: var(--ink-white); letter-spacing: -3px; margin-bottom: -6px;
  }
  .brand-tm { font-family: var(--brand); font-weight: 800; font-size: 18px; color: var(--ink-white); align-self: flex-start; margin-left: -24px; margin-top: 110px; }

  .gateway {
    position: absolute; left: 109px; top: 445px; width: 1009px; height: 308px;
    background: linear-gradient(180deg, var(--panel-top) 0%, #2e6679 30%, var(--panel-mid) 50%, var(--panel-low) 72%, var(--panel-low) 100%);
    border: 3px solid #e8eef0; border-bottom: none;
    box-shadow: 0 0 14px 3px rgba(255,255,255,0.55);
    display: flex;
  }
  .gateway-divider { position: absolute; left: 506px; top: 16px; width: 3px; height: 273px; background: var(--ink-white); }
  .gateway-option { position: relative; width: 50%; }
  .gateway-heading {
    position: absolute; top: 14px; width: 100%;
    font-family: var(--script); font-size: 44px; line-height: 60px; color: var(--ink-white); text-align: center;
  }
  .join .gateway-heading { left: -294px; width: 1009px; left: auto; }
  .gateway-button {
    position: absolute; top: 153px; width: 254px; height: 64px;
    background: var(--button-green);
    border: 2px solid var(--button-ring);
    box-shadow: inset 0 0 0 3px var(--button-edge), inset 0 -6px 8px rgba(120,90,20,0.35);
    font-family: var(--script); font-size: 36px; color: var(--ink-white);
    display: flex; align-items: center; justify-content: center;
    text-shadow: 0 1px 2px rgba(0,0,0,0.3);
  }

  .info-tabs { position: absolute; left: 70px; top: 0; }
  .info-tab {
    position: absolute; left: 0; width: 247px; height: 59px;
    background: linear-gradient(90deg, var(--tab-pink) 0%, #f3a3b0 45%, var(--tab-cream) 100%);
    font-family: var(--serif); font-style: italic; font-size: 37px; color: var(--ink-white);
    display: flex; align-items: center; justify-content: center; line-height: 1;
  }
</style>
</head>
<body>
<div class="page">
  <section class="stage">
    <p class="coming-soon">COMING SOON</p>

    <div class="brand">
      <div class="brand-mark"></div>
      <span class="brand-name">Parcelnook.com</span>
    </div>

    <div class="gateway">
      <div class="gateway-option join">
        <h2 class="gateway-heading" style="left:-60px;width:540px;">Want to<br>join us</h2>
        <a class="gateway-button" style="left:79px;">Signup/Login</a>
      </div>
      <div class="gateway-divider"></div>
      <div class="gateway-option visit">
        <h2 class="gateway-heading" style="left:-60px;width:630px;">Want to<br>visit a shop</h2>
        <a class="gateway-button" style="left:151px;">Select a shop</a>
      </div>
    </div>
  </section>
  <div class="stage-band"></div>

  <nav class="info-tabs">
    <a class="info-tab" style="top:803px;">Contact us</a>
    <a class="info-tab" style="top:891px;">Mission</a>
    <a class="info-tab" style="top:989px;">About us</a>
  </nav>
</div>
</body>
</html>
```